Book cover

I am working with my publisher to publish my book They came up with a book cover but I don't like it. I want to see different designs. The book Title is Brightwater the subtitle Ways to Guide Teams Through Storms with Poise, Purpose & Pace by Marlene T. Ostrowski
I want to use my Brand Colors including the blue. I am uploading the covers of my other book. This is a professional leadership book. The publisher will make the cover when providing them a new design. the Brightwater one is one I played with on Canva. I would like more color and to incorporate the blue. I want a spot at the top where I can write a quote. Brightwater is one word in the text so should be the same on the cover. I want the cover to show energy movement and am open to an image too. I am attaching logos for the feel of the brand and brand rgb codes.

```html
<!DOCTYPE html>
<html lang="en">
<head>
<meta charset="utf-8">
<title>Brightwater — Book Cover Spread</title>
<link rel="stylesheet" href="https://fonts.googleapis.com/css2?family=Anton&family=Arimo&family=Crimson+Pro:wght@400;600&family=Great+Vibes&display=swap">
<style>
  :root {
    --page-bg: #ffffff;
    --cover-deep: #1a4f93;
    --cover-mid: #2461ad;
    --cover-light: #4d84cc;
    --portrait-tone: #5c8fd3;
    --accent: #e0553b;
    --ink-light: #ffffff;
    --spine-bg: #ffffff;
    --spine-ink: #5a5a5a;
  }
  html, body {
    margin: 0;
    padding: 0;
    width: 780px;
    height: 1200px;
    overflow: hidden;
    background: var(--page-bg);
  }
  .canvas {
    position: relative;
    width: 780px;
    height: 1200px;
  }
  .cover-spread {
    position: absolute;
    left: 20px;
    top: 340px;
    width: 740px;
    height: 520px;
    display: block;
  }
  .title-block { font-family: "Anton", "Oswald", sans-serif; fill: var(--ink-light); }
  .spine-title { font-family: "Crimson Pro", "Times New Roman", serif; font-weight: 400; fill: var(--spine-ink); }
  .quote-text { font-family: "Crimson Pro", "Times New Roman", serif; font-weight: 400; font-size: 23px; fill: var(--ink-light); }
  .quote-author { fill: var(--accent); }
  .subtitle { font-family: "Crimson Pro", "Times New Roman", serif; font-weight: 400; font-size: 27px; fill: var(--ink-light); letter-spacing: 0.5px; }
  .byline { font-family: "Crimson Pro", "Times New Roman", serif; font-weight: 400; font-size: 20px; fill: var(--ink-light); }
  .author-name { font-family: "Great Vibes", cursive; font-size: 46px; fill: var(--ink-light); }
  .back-copy { font-family: "Arimo", Arial, sans-serif; font-size: 14.5px; fill: var(--ink-light); }
  .publisher-name { font-family: "Crimson Pro", "Times New Roman", serif; font-weight: 400; font-size: 22px; fill: var(--ink-light); letter-spacing: 1px; }
  .frame-line { fill: none; stroke: var(--accent); stroke-width: 2.5; }
</style>
</head>
<body>
<main class="canvas">
  <svg class="cover-spread" viewBox="0 0 1372 965" xmlns="http://www.w3.org/2000/svg" aria-label="Brightwater book cover spread: back cover, spine and front cover">
    <defs>
      <linearGradient id="back-gradient" x1="0" y1="0" x2="1" y2="1">
        <stop offset="0" stop-color="var(--cover-light)"/>
        <stop offset="0.45" stop-color="var(--cover-mid)"/>
        <stop offset="1" stop-color="var(--cover-deep)"/>
      </linearGradient>
      <linearGradient id="front-gradient" x1="0" y1="0" x2="0.8" y2="1">
        <stop offset="0" stop-color="var(--cover-mid)"/>
        <stop offset="1" stop-color="var(--cover-deep)"/>
      </linearGradient>
      <radialGradient id="portrait-gradient" cx="0.75" cy="0.35" r="0.7">
        <stop offset="0" stop-color="var(--portrait-tone)"/>
        <stop offset="0.6" stop-color="var(--cover-mid)" stop-opacity="0.7"/>
        <stop offset="1" stop-color="var(--cover-deep)" stop-opacity="0"/>
      </radialGradient>
    </defs>

    <g class="back-cover">
      <rect width="644" height="965" fill="url(#back-gradient)"/>
      <text class="back-copy" text-anchor="middle">
        <tspan x="322" y="280">Lorem ipsum dolor sit amet, consectetuer adipiscing elit, sed diam</tspan>
        <tspan x="322" y="301">nonummy nibh euismod tincidunt ut laoreet dolore magna aliquam</tspan>
        <tspan x="322" y="322">erat volutpat. Ut wisi enim ad minim veniam, quis nostrud exerci tation</tspan>
        <tspan x="322" y="343">ullamcorper suscipit lobortis nisl ut aliquip ex ea commodo consequat.</tspan>
        <tspan x="322" y="364">Duis autem vel eum iriure dolor in hendrerit in vulputate velit esse</tspan>
        <tspan x="322" y="385">molestie consequat, vel illum dolore eu feugiat nulla facilisis at vero</tspan>
        <tspan x="322" y="406">eros et accumsan et iusto odio dignissim qui blandit praesent</tspan>
        <tspan x="322" y="427">luptatum zzril delenit augue duis dolore te feugait nulla facilisi.</tspan>
        <tspan x="322" y="469">Lorem ipsum dolor sit amet, cons ectetuer adipiscing elit, sed diam</tspan>
        <tspan x="322" y="490">nonummy nibh euismod tincidunt ut laoreet dolore magna aliquam</tspan>
        <tspan x="322" y="511">erat volutpat. Ut wisi enim ad minim veniam, quis nostrud exerci tation</tspan>
        <tspan x="322" y="532">ullamcorper suscipit lobortis nisl ut aliquip ex ea commodo consequat.</tspan>
        <tspan x="322" y="553">Lorem ipsum dolor sit amet, consectetuer adipiscing elit, sed diam</tspan>
        <tspan x="322" y="574">nonummy nibh euismod tincidunt ut laoreet dolore magna aliquam</tspan>
        <tspan x="322" y="595">erat volutpat. Ut wisi enim ad minim veniam, quis nostrud exerci tation</tspan>
        <tspan x="322" y="616">ullamcorper suscipit lobortis nisl ut aliquip ex ea commodo consequat.</tspan>
        <tspan x="322" y="637">Duis autem vel eum iriure dolor in hendrerit in vulputate velit esse</tspan>
        <tspan x="322" y="658">molestie consequat, vel illum dolore eu feugiat nulla facilisis at vero</tspan>
        <tspan x="322" y="679">eros et accumsan et iusto odio dignissim qui blandit praesent</tspan>
        <tspan x="322" y="700">luptatum zzril</tspan>
      </text>
      <text class="publisher-name" x="322" y="912" text-anchor="middle">Ashford Books</text>
    </g>

    <g class="spine" transform="translate(644 0)">
      <rect width="86" height="965" fill="var(--spine-bg)"/>
      <text class="spine-title" font-size="58" transform="translate(25 230) rotate(90)" textLength="500" lengthAdjust="spacingAndGlyphs">BRIGHTWATER</text>
    </g>

    <g class="front-cover" transform="translate(730 0)">
      <rect width="642" height="965" fill="url(#front-gradient)"/>
      <rect class="portrait-area" x="300" y="0" width="342" height="965" fill="url(#portrait-gradient)" role="img" aria-label="Painted portrait of the author in blue tones"/>

      <text class="title-block" font-size="162" transform="translate(118 925) rotate(-90)" textLength="895" lengthAdjust="spacingAndGlyphs">BRIGHTWATER</text>

      <g class="quote-frame">
        <path class="frame-line" d="M142 0 V182 Q142 212 172 212 H385"/>
        <path class="frame-line" d="M215 75 H472 Q505 75 505 108 V350"/>
        <g class="quote-mark-open">
          <circle cx="176" cy="77" r="9" fill="var(--accent)"/>
          <path d="M170 73 Q170 60 182 57" stroke="var(--accent)" stroke-width="5" fill="none"/>
          <circle cx="197" cy="77" r="9" fill="var(--ink-light)"/>
          <path d="M191 73 Q191 60 203 57" stroke="var(--ink-light)" stroke-width="5" fill="none"/>
        </g>
        <g class="quote-mark-close">
          <circle cx="428" cy="208" r="9" fill="var(--ink-light)"/>
          <path d="M434 212 Q434 225 422 228" stroke="var(--ink-light)" stroke-width="5" fill="none"/>
          <circle cx="449" cy="208" r="9" fill="var(--accent)"/>
          <path d="M455 212 Q455 225 443 228" stroke="var(--accent)" stroke-width="5" fill="none"/>
        </g>
        <text class="quote-text">
          <tspan x="164" y="118">Bright Water is the essential</tspan>
          <tspan x="164" y="146">playbook to turn uncertainty into</tspan>
          <tspan x="164" y="174">possibility <tspan class="quote-author" dx="8">Marlene T. Ostrowski</tspan></tspan>
        </text>
      </g>

      <text class="subtitle">
        <tspan x="150" y="762">WAYS TO GUIDE TEAMS</tspan>
        <tspan x="150" y="794">THROUGH STORMS WITH POISE,</tspan>
        <tspan x="150" y="826">PURPOSE &amp; PACE</tspan>
      </text>
      <text class="byline" x="150" y="856">BY</text>
      <text class="author-name" x="150" y="905">Marlene T. Ostrowski</text>
    </g>
  </svg>
</main>
</body>
</html>
```